Calvera fine stockings - sexy cardboard box design needed!

We need a packaging design for a new online company based in Sydney called 'Calvera Hosiery'. We will be selling sexy stockings to our customers by Italian designers. We mainly feature lace stockings, an example of which, can be seen here:
http://www.brontevassipelli.example/italy-FASHION-WINTER

The design should be a cardboard pull out box, black in colour with the logo on the cover. We are looking for the logo to communicate sophistication and sexiness.

Examples of cardboard box shapes we would like are:
http://www.tradoquel.example/product-gs/583016274/High_quality_drawer_paper_box.html

http://www.tradoquel.example/product-gs/639152487/Cardboard_drawer_box.html

29 December:
I submitted a note when I extended the deadline, but cannot see it, so will write here for clarification. It has been difficult to choose the best design as the designs submitted were of such high quality. I want to have some people judge the designs, but because of the Christmas Season I have extended the deadline so that this can be done. Thanks.

Target Market(s)

The working professional woman.

Industry/Entity Type

Fashion

Requirements
Must have
• The words "Calvera Hosiery" on the cover of the box.

The box should be a sliding drawer.

The box size should be: (22*15*2.5cm).

Washing instructions and recycling logos on the back of the box. See example of uploaded file.

Nice to have
• It would be nice to have the background of the box a dark colour, maybe charcoal? But we are open to all ideas.
Should not have
• A stock photo on cover of box.

```html
<!DOCTYPE html>
<html lang="en">
<head>
<meta charset="utf-8">
<title>Calvera Hosiery — Drawer Box Cover</title>
<link rel="stylesheet" href="https://fonts.googleapis.com/css2?family=Questrial&display=swap">
<style>
  :root {
    --stage: #d9d8d8;
    --box-black: #0b0b0b;
    --gold-light: #f3d64a;
    --gold-mid: #d6aa1c;
    --gold-dark: #a87a10;
    --lacquer-red: #820000;
    --brass: #c98a1e;
    --logo-white: #ffffff;
  }
  * { margin: 0; padding: 0; box-sizing: border-box; }
  html, body {
    width: 1200px;
    height: 818px;
    overflow: hidden;
    background: var(--stage);
  }
  .box-cover {
    position: absolute;
    left: 175px;
    top: 70px;
    width: 850px;
    height: 667px;
    background: var(--box-black);
  }
  .cover-field {
    position: absolute;
    left: 0;
    top: 0;
    width: 100%;
    height: 510px;
    background: var(--box-black);
  }
  .brand-name {
    position: absolute;
    left: 0;
    width: 100%;
    top: 262px;
    text-align: center;
    font-family: "Questrial", sans-serif;
    font-size: 16px;
    letter-spacing: 3px;
    color: var(--logo-white);
    text-transform: lowercase;
  }
  .gold-band {
    position: absolute;
    left: 0;
    top: 510px;
    width: 100%;
    height: 43px;
    background: linear-gradient(180deg, var(--gold-light) 0%, var(--gold-mid) 55%, var(--gold-dark) 100%);
  }
  .red-base {
    position: absolute;
    left: 0;
    top: 553px;
    width: 100%;
    height: 114px;
    background: var(--lacquer-red);
  }
  .drawer-pull {
    position: absolute;
    left: 403px;
    top: 35px;
    width: 44px;
    height: 62px;
    border-radius: 22px;
    background: var(--brass);
  }
</style>
</head>
<body>
  <main class="box-cover">
    <section class="cover-field">
      <p class="brand-name">Calvera Hosiery</p>
    </section>
    <div class="gold-band" role="img" aria-label="Woven gold braid trim band"></div>
    <section class="red-base">
      <div class="drawer-pull" role="img" aria-label="Ornamental brass lion-head door knocker drawer pull"></div>
    </section>
  </main>
</body>
</html>
```